About the book: It is an A5 size book, small 40 pages miniguide
Book title: The handy pocket primer on housing loans
Book subtitle: The quick road to riches
Author: Rod Pemberton
Back cover content: Please see attached word document "back page"
Colours: Our company logo should go at the back of the book. One colour we can't use is red. As this is a finance book the red colour is seen negatively. may be light green? you are the expert.
I think lots of white space will work well.
NOTE: please read the back cover notes to get an understanding of what the book is about. It educates readers about finance in property investing. It makes sense that image used combines 'property' and 'finance'. please read back page document attached.
NOTE: it is a small A5 , 40 page book . Its a miniguide rather than a book .

Reason: Dear designers, Thank you for submitting your work over the last few days. Unfortunately we haven't been able to get back to you regarding the final selection of design as the Author of the book has been away on leave with his family without reliable internet access. He is now back and will be giving feedback as we go. We apologise for the time extension. Unfortunately the site didn’t allow me to limit the extension for less than 5 days but we may not require that long. Thanks again. Tova

Reason: We apologies we hadn't finalized a decision on this project due to the person from our end being away. We would like to finalise this design as soon as possible.

Target Market(s)

22 - 45 age group. Most fall between 30-40. Both male and female. couples , individuals etc ...

Industry/Entity Type

Finance

Font styles to use
Other font styles liked:
• sabon/Aeriel. Let me know if any other suggestions.

Requirements
Nice to have
• use green colour if possible but not essential.

```html
<!DOCTYPE html>
<html lang="en">
<head>
<meta charset="utf-8">
<title>The handy pocket primer on housing loans — Rod Pemberton</title>
<link rel="stylesheet" href="https://fonts.googleapis.com/css2?family=Anton&family=Raleway:wght@300;400&family=Montserrat:wght@800&display=swap">
<style>
  :root {
    --backdrop: #1f1f1f;
    --paper: #ffffff;
    --green: #2f7a0b;
    --green-mid: #3f9215;
    --green-light: #5cb81e;
    --ink: #111111;
    --rule: #555555;
  }
  html, body {
    margin: 0;
    padding: 0;
    width: 1200px;
    height: 1148px;
    overflow: hidden;
    background: var(--backdrop);
  }
  .canvas {
    position: relative;
    width: 1200px;
    height: 1148px;
  }
  .cover {
    position: absolute;
    left: 240px;
    top: 65px;
    width: 720px;
    height: 1018px;
    background: var(--paper);
    overflow: hidden;
  }
  .cover-art {
    position: absolute;
    left: 160px;
    top: 60px;
    width: 400px;
    height: 280px;
    background: linear-gradient(180deg, var(--green-mid) 0%, var(--green) 100%);
  }
  .title {
    position: absolute;
    top: 370px;
    left: 0;
    width: 720px;
    margin: 0;
    text-align: center;
    font-weight: normal;
  }
  .title-lead {
    display: block;
    font-family: "Raleway", Arial, sans-serif;
    font-weight: 300;
    font-size: 50px;
    line-height: 1.02;
    letter-spacing: 1px;
    color: var(--ink);
    text-transform: uppercase;
  }
  .title-main {
    display: block;
    font-family: "Anton", "Arial Narrow", sans-serif;
    font-size: 128px;
    line-height: 0.98;
    color: var(--green);
    text-transform: uppercase;
    margin-top: 4px;
  }
  .subtitle {
    position: absolute;
    top: 762px;
    left: 130px;
    width: 460px;
    margin: 0;
    padding: 10px 0;
    border-top: 2px solid var(--rule);
    border-bottom: 2px solid var(--rule);
    text-align: center;
    font-family: "Raleway", Arial, sans-serif;
    font-weight: 400;
    font-size: 34px;
    line-height: 1.2;
    color: var(--ink);
  }
  .author-band {
    position: absolute;
    left: 0;
    bottom: 0;
    width: 720px;
    height: 160px;
    background: var(--green);
    border-bottom: 14px solid var(--green-light);
    box-sizing: border-box;
    display: flex;
    align-items: center;
    justify-content: center;
  }
  .author {
    margin: 0;
    font-family: "Montserrat", Arial, sans-serif;
    font-weight: 800;
    font-size: 54px;
    letter-spacing: 1px;
    color: var(--paper);
    text-transform: uppercase;
  }
</style>
</head>
<body>
<div class="canvas">
  <article class="cover">
    <div class="cover-art" role="img" aria-label="Illustration of a green house with a dollar sign, crossed by a rising trend line"></div>

    <h1 class="title">
      <span class="title-lead">The handy pocket</span>
      <span class="title-lead">primer on</span>
      <span class="title-main">Housing</span>
      <span class="title-main">Loans</span>
    </h1>

    <p class="subtitle">The Quick Road To Riches</p>

    <footer class="author-band">
      <p class="author">Rod Pemberton</p>
    </footer>
  </article>
</div>
</body>
</html>
```